QVR business card

Need a business card for a company that provides instructional design and elearning development services. The website is here: http://quorvane.studio/

I'm attaching a current logo, as well as the old business card design. While I like to keep it clean, the old design is too simplistic for my liking. The only idea I want to reuse from the old design is placing industry jargon on the back of the card, just need a better way to present it. But if you have other ideas for the back--feel free to experiment.

Please use the colors complementary to the color we have on the website. Thank you!

```html
<!DOCTYPE html>
<html lang="en">
<head>
<meta charset="utf-8">
<title>QVR business card</title>
<link rel="stylesheet" href="https://fonts.googleapis.com/css2?family=Source+Sans+3:wght@400;600;700&display=swap">
<style>
  :root {
    --teal: #14b1ad;
    --white: #ffffff;
    --ink: #2b2b2b;
    --stage: #eceae7;
    --font: "Source Sans 3", sans-serif;
  }
  * { margin: 0; padding: 0; box-sizing: border-box; }
  html, body { width: 1200px; height: 900px; overflow: hidden; }
  body { background: var(--stage); font-family: var(--font); position: relative; }

  .card { position: absolute; border-radius: 16px; overflow: hidden; box-shadow: 0 6px 18px rgba(0,0,0,.12); }

  /* Front */
  .card-front { left: 78px; top: 35px; width: 588px; height: 362px; background: var(--white); }
  .card-front .band { position: absolute; left: 0; top: 28px; width: 100%; height: 99px; background: var(--teal); }
  .card-front .mark-circle { position: absolute; left: 202px; top: 8px; width: 160px; height: 160px; border-radius: 50%; background: var(--white); }
  .card-front .brand { position: absolute; left: 0; width: 100%; top: 160px; text-align: center; font-size: 84px; font-weight: 700; color: var(--teal); letter-spacing: 6px; line-height: 1; }
  .person { position: absolute; left: 43px; top: 243px; font-size: 21px; font-weight: 700; color: var(--teal); }
  .contacts { position: absolute; right: 34px; top: 260px; list-style: none; text-align: right; }
  .contacts li { font-size: 15.5px; color: var(--ink); line-height: 21.5px; display: flex; align-items: center; justify-content: flex-end; gap: 8px; }
  .contacts svg { width: 13px; height: 13px; fill: var(--teal); }

  /* Back */
  .card-back { left: 390px; top: 506px; width: 564px; height: 350px; background: var(--teal); color: var(--white); }
  .card-back .band { position: absolute; left: 0; top: 24px; width: 100%; height: 82px; background: var(--white); }
  .card-back .mark-circle { position: absolute; left: 206px; top: 0; width: 136px; height: 136px; border-radius: 50%; background: var(--teal); }
  .card-back .brand { position: absolute; left: 0; width: 100%; top: 112px; text-align: center; font-size: 64px; font-weight: 700; letter-spacing: 5px; line-height: 1; }
  .help-title { position: absolute; left: 0; width: 100%; top: 198px; text-align: center; font-size: 18px; font-weight: 700; letter-spacing: .3px; }
  .services { position: absolute; left: 0; width: 100%; top: 233px; list-style: none; }
  .services li { display: flex; justify-content: center; align-items: center; gap: 12px; font-size: 15.5px; font-weight: 600; height: 36.5px; }
  .services .dot { width: 7px; height: 7px; border-radius: 50%; background: var(--white); }
</style>
</head>
<body>
  <section class="card card-front" aria-label="Business card front">
    <div class="band"></div>
    <div class="mark-circle"></div>
    <div class="brand">QVR</div>
    <p class="person">Daniel Ferrow</p>
    <ul class="contacts">
      <li>555-014-2387
        <svg viewBox="0 0 24 24" aria-hidden="true"><path d="M6.6 10.8a15.1 15.1 0 0 0 6.6 6.6l2.2-2.2a1 1 0 0 1 1-.25 11.4 11.4 0 0 0 3.6.57 1 1 0 0 1 1 1V20a1 1 0 0 1-1 1A17 17 0 0 1 3 4a1 1 0 0 1 1-1h3.5a1 1 0 0 1 1 1c0 1.25.2 2.45.57 3.57a1 1 0 0 1-.25 1z"/></svg></li>
      <li>dferrow@quorvane.studio
        <svg viewBox="0 0 24 24" aria-hidden="true"><path d="M2 5h20v14H2z M2 5l10 8 10-8" fill="var(--teal)" stroke="#fff" stroke-width="1.6"/></svg></li>
      <li>www.quorvane.studio
        <svg viewBox="0 0 24 24" aria-hidden="true"><circle cx="12" cy="12" r="11"/><path d="M1 12h22M12 1c4 4 4 18 0 22M12 1c-4 4-4 18 0 22" fill="none" stroke="#fff" stroke-width="1.5"/></svg></li>
    </ul>
  </section>

  <section class="card card-back" aria-label="Business card back">
    <div class="band"></div>
    <div class="mark-circle"></div>
    <div class="brand">QVR</div>
    <h2 class="help-title">HOW CAN WE HELP?</h2>
    <ul class="services">
      <li>Mobile Learning Scorm <span class="dot"></span> Instructional Design Lms</li>
      <li>Moocs Elearning Html5 <span class="dot"></span> Adult Learning Theory</li>
      <li>Gamification Classroom <span class="dot"></span> Xapi Blended Learning</li>
    </ul>
  </section>
</body>
</html>
```